Kestrel Facilities Business Card Design

We would now like to design business cards with the new Kestrel Facilities logo

Target Market(s)

Professional

Industry/Entity Type

Professional services

Contact Information for Business Card

Employee name, title, phone number, email address, corporate office address and logo.

Font styles to use
Sans Serif

Colors
0054AA
0677BA
7BADD7
CADEEF
E8F1F8

Requirements
Must have
• My logo
Should not have
• any other pictures or images besides my logo

```html
<!DOCTYPE html>
<html lang="en">
<head>
<meta charset="utf-8">
<title>Kestrel Facilities Business Card</title>
<link href="https://fonts.googleapis.com/css2?family=Open+Sans:wght@400;600;700&display=swap" rel="stylesheet">
<style>
  :root {
    --brand-blue: #3a7bbf;
    --brand-deep: #0054aa;
    --ink: #4a4a4a;
    --paper: #ffffff;
    --backdrop: #d9d9d7;
  }
  * { margin: 0; padding: 0; box-sizing: border-box; }
  html, body { width: 1200px; height: 801px; overflow: hidden; }
  body {
    background: var(--backdrop);
    font-family: "Open Sans", Arial, sans-serif;
    display: flex;
    align-items: center;
    justify-content: center;
    gap: 60px;
  }
  .card {
    width: 525px;
    height: 300px;
    position: relative;
    box-shadow: 0 6px 18px rgba(0,0,0,0.18);
  }
  .card--front { background: var(--paper); border-bottom: 3px solid var(--brand-blue); }
  .card--back {
    background: var(--brand-blue);
    display: flex;
    align-items: center;
    justify-content: center;
  }
  .wordmark {
    display: flex;
    align-items: center;
    gap: 10px;
    font-weight: 700;
    color: var(--brand-blue);
    line-height: 1.05;
    text-transform: uppercase;
    letter-spacing: 0.04em;
  }
  .wordmark__square { background: currentColor; flex: none; }
  .card--front .wordmark { position: absolute; left: 34px; top: 40px; font-size: 22px; }
  .card--front .wordmark__square { width: 26px; height: 26px; }
  .card--back .wordmark { color: var(--paper); font-size: 40px; gap: 18px; }
  .card--back .wordmark__square { width: 48px; height: 48px; }

  .person { position: absolute; right: 34px; top: 40px; text-align: right; }
  .person__name { color: var(--brand-blue); font-weight: 700; font-size: 20px; letter-spacing: 0.01em; }
  .person__title { color: var(--ink); font-size: 12px; margin-top: 2px; }

  .divider {
    position: absolute; left: 34px; right: 34px; top: 150px;
    height: 1.5px; background: var(--brand-blue);
  }

  .contact { position: absolute; left: 34px; top: 172px; list-style: none; }
  .contact li {
    display: flex; align-items: center; gap: 8px;
    color: var(--ink); font-size: 13.5px; line-height: 24px;
  }
  .contact svg { width: 11px; height: 11px; fill: var(--brand-blue); flex: none; }

  .address {
    position: absolute; right: 34px; top: 172px;
    text-align: right; color: var(--ink); font-size: 13.5px; line-height: 22px;
    font-style: normal;
  }
</style>
</head>
<body>
  <section class="card card--front">
    <div class="wordmark"><span class="wordmark__square"></span><span>Kestrel<br>Facilities</span></div>
    <div class="person">
      <p class="person__name">DANIEL HARROW</p>
      <p class="person__title">CEO</p>
    </div>
    <div class="divider"></div>
    <ul class="contact">
      <li><svg viewBox="0 0 12 12"><path d="M3 1l2 2.5-1.2 1.2a7 7 0 0 0 3.5 3.5L8.5 7 11 9l-1.3 1.8C5.5 11 1 6.5 1.2 2.3z"/></svg>555-214-3380</li>
      <li><svg viewBox="0 0 12 12"><path d="M1 3h10v6H1z M1 3l5 3.5L11 3" fill="none" stroke="#3a7bbf" stroke-width="1.4"/></svg>dharrow@kestrelgroup.net</li>
      <li><svg viewBox="0 0 12 12"><circle cx="6" cy="6" r="5"/></svg>www.kestrelgroup.net</li>
    </ul>
    <address class="address">418 Meridian Road<br>Eastbrook, MA 02407</address>
  </section>

  <section class="card card--back">
    <div class="wordmark"><span class="wordmark__square"></span><span>Kestrel<br>Facilities</span></div>
  </section>
</body>
</html>
```